SnackOrbit!!! A Vending Machine Business Looking for an attractive website.

We are a vending machine business in Northern Michigan. We have changed our name and have rebranded our company. We would like an attractive website that shares who we are, what services we provide, the products we offer in our machines, along with a form businesses can fill out to see if they are a good fit for our company. I would like to have a Home Page, About SnackOrbit, Why Choose SnackOrbit?, Products & Services, Contact Us (With a Login Option), and a page with a questionnaire for thos interested in getting a FREE Vending Machine.

Target Market(s)

Businesses, Campgrounds, Schools, and many more in Northern Michigan

Industry/Entity Type

Vending Machines

Coding

Coded - Design and coding required

Number of Pages Required

5+ page

Requirements
Must have
• An inviting and enticing Home Page. I want to get my potential clients engaged in our website.
Nice to have
• Possibly background photos from Northern Michigan
Should not have
• A corporate feel. I do not want a boring website.

```html
<!DOCTYPE html>
<html lang="en">
<head>
<meta charset="utf-8">
<title>SnackOrbit — Vending Machines in Northern Michigan</title>
<link rel="stylesheet" href="https://fonts.googleapis.com/css2?family=Rubik:wght@700;800;900&family=Josefin+Sans:wght@300;400;600&display=swap">
<style>
:root{
  --navy:#1f2566;
  --navy-deep:#1b1f57;
  --green:#2d5a27;
  --green-bright:#3fa535;
  --ink:#333;
  --muted:#555;
  --white:#fff;
  --hero-bg:#ececec;
}
*{box-sizing:border-box;margin:0;padding:0}
html,body{width:1200px;height:4326px;overflow:hidden}
body{position:relative;background:var(--white);font-family:"Josefin Sans",sans-serif;color:var(--ink)}
.abs{position:absolute}
.display{font-family:"Rubik",sans-serif;font-weight:800}
.btn{position:absolute;display:flex;align-items:center;justify-content:center;border-radius:22px;background:var(--green);color:var(--white);font-family:"Rubik",sans-serif;font-weight:800;font-size:14px;text-transform:uppercase;letter-spacing:.2px}
.ph{position:absolute}

/* header */
.site-header{position:absolute;left:0;top:0;width:1200px;height:81px;background:var(--white)}
.brand{position:absolute;left:111px;top:20px;font-family:"Rubik",sans-serif;font-weight:800;font-size:32px;color:var(--navy);letter-spacing:-.5px}
.nav{position:absolute;left:297px;top:34px;display:flex;gap:26px;font-size:15px;color:var(--ink)}
.nav .active{color:var(--green);position:relative}
.nav .active::before{content:"";position:absolute;left:-2px;right:-2px;top:-34px;height:3px;background:var(--navy)}
.login{left:968px;top:23px;width:120px;height:41px}

/* hero */
.hero{position:absolute;left:0;top:81px;width:1200px;height:590px;background:linear-gradient(180deg,#f2f2f2,#e4e4e4)}
.hero-art{left:92px;top:80px;width:580px;height:500px;background:linear-gradient(90deg,#c8202a 0%,#b81a23 45%,#d92b33 55%,#c41e27 100%);border-radius:6px}
.hero-welcome{position:absolute;right:112px;top:168px;font-size:33px;color:var(--green)}
.hero-title{position:absolute;right:112px;top:212px;font-size:96px;color:var(--navy);letter-spacing:-2px;line-height:1}
.hero-lead{position:absolute;right:112px;top:330px;width:400px;text-align:right;font-size:22px;line-height:29px;color:var(--ink)}
.hero-cta{left:812px;top:392px;width:276px;height:40px;font-size:14px}

/* who */
.who-img{left:111px;top:770px;width:447px;height:338px;background:linear-gradient(135deg,#8fb2a9,#5f8a85)}
.who h2{position:absolute;left:643px;top:762px;font-size:40px;color:var(--navy)}
.who p{position:absolute;left:643px;top:826px;width:445px;font-size:16.5px;line-height:28.5px;color:var(--ink)}
.who .btn{left:643px;top:1060px;width:140px;height:41px}

/* why */
.why{position:absolute;left:0;top:1210px;width:1200px;height:807px;background:linear-gradient(180deg,#2a3277 0%,#26306e 60%,#2b3572 100%)}
.why h2{position:absolute;left:0;width:1200px;top:50px;text-align:center;font-size:38px;color:var(--white)}
.why-machine{position:absolute;left:443px;top:144px;width:315px;height:571px;border:2px solid #c9cde6;background:linear-gradient(90deg,#2c8ac9,#3aa0d9)}
.why-item{position:absolute;width:290px;color:var(--white)}
.why-item h3{font-family:"Rubik",sans-serif;font-weight:800;font-size:18px;line-height:26px}
.why-item p{font-size:16px;line-height:26px;margin-top:8px;font-weight:300}
.why-item a{display:inline-block;margin-top:6px;font-family:"Rubik",sans-serif;font-weight:700;font-size:14px;color:var(--white);text-decoration:underline}
.why-item.right{text-align:right;width:300px}
.why-icon{position:absolute}

/* services */
.services h2{position:absolute;left:0;width:1200px;top:2102px;text-align:center;font-size:38px;color:var(--navy)}
.tab{position:absolute;top:2190px;height:42px;border:1.5px solid var(--ink);border-radius:21px;display:flex;align-items:center;justify-content:center;font-family:"Rubik",sans-serif;font-weight:800;font-size:14px;color:var(--ink)}
.tab.active{background:var(--green);border-color:var(--green);color:var(--white)}
.svc-title{position:absolute;left:111px;top:2306px;font-size:26px;color:var(--navy)}
.svc-icon{left:308px;top:2278px;width:76px;height:68px;background:linear-gradient(135deg,#2d5a27,#1f2566);border-radius:8px}
.svc-text{position:absolute;left:111px;top:2370px;width:530px;font-size:16.5px;line-height:28.3px;color:var(--muted)}
.svc-btn{left:111px;top:2666px;width:140px;height:41px}
.svc-machine{left:760px;top:2249px;width:320px;height:486px;background:linear-gradient(90deg,#b9bcc2,#e3e5e8 40%,#2a5fb0 100%);border-radius:6px}

/* products */
.products{position:absolute;left:0;top:2806px;width:1200px;height:724px;background:linear-gradient(180deg,#262f70,#2a3576)}
.products h2{position:absolute;left:0;width:1200px;top:70px;text-align:center;font-size:36px;color:var(--white)}
.card{position:absolute;top:149px;width:316px}
.card-img{width:316px;height:309px}
.card h3{margin-top:28px;font-family:"Rubik",sans-serif;font-weight:800;font-size:24px;line-height:29px;color:var(--green-bright)}
.card h3.alt{color:var(--white)}
.card .price{font-family:"Rubik",sans-serif;font-weight:800;font-size:26px;color:var(--white);margin-top:3px}
.card .btn{position:relative;margin-top:6px;width:115px;height:38px;font-size:13px}
.badge{position:absolute;width:36px;height:36px;border-radius:50%;background:var(--white);display:flex;align-items:center;justify-content:center;font-size:10px;font-weight:600;color:var(--ink)}
.dots{position:absolute;top:647px;left:572px;display:flex;gap:12px}
.dots span{width:9px;height:9px;border-radius:50%;background:var(--white)}
.dots span.on{background:var(--green-bright)}

/* cta */
.cta{position:absolute;left:0;top:3530px;width:1200px;height:333px;background:var(--green);text-align:center;color:var(--white)}
.cta h2{position:absolute;left:150px;width:900px;top:62px;font-size:37px;line-height:49px}
.cta p{position:absolute;left:150px;width:900px;top:168px;font-size:21px;line-height:35px;font-weight:400}
.cta .btn{left:535px;top:242px;width:130px;height:40px;background:var(--white);color:var(--ink);font-size:13px}

/* footer */
.site-footer{position:absolute;left:0;top:3863px;width:1200px;height:463px;background:var(--navy-deep);color:var(--white)}
.foot-brand{position:absolute;left:111px;top:100px;font-family:"Rubik",sans-serif;font-weight:800;font-size:76px;letter-spacing:-2px;color:var(--white)}
.social{position:absolute;top:242px;width:52px;height:52px;border-radius:50%;background:var(--white)}
.foot-col h4{position:absolute;top:126px;font-family:"Rubik",sans-serif;font-weight:800;font-size:20px}
.foot-links{position:absolute;left:619px;top:178px;list-style:none;font-size:16px;line-height:35.5px}
.contact-row{position:absolute;left:845px;display:flex;align-items:center;gap:14px;font-size:15px;line-height:21px}
.contact-row i{width:46px;height:46px;border-radius:50%;background:var(--green);display:flex;align-items:center;justify-content:center;flex:none}
.copyright{position:absolute;left:0;width:1200px;top:398px;text-align:center;font-size:17px}
</style>
</head>
<body>

<header class="site-header">
  <div class="brand">SnackOrbit</div>
  <nav class="nav">
    <span class="active">Home</span>
    <span>About SnackOrbit</span>
    <span>Why Choose SnackOrbit?</span>
    <span>Products &amp; Services</span>
    <span>Contact Us</span>
  </nav>
  <a class="btn login">Login</a>
</header>

<section class="hero">
  <div class="ph hero-art" role="img" aria-label="Two red vending machines, a drink machine and a snack machine, in front of a white brick wall"></div>
  <div class="hero-welcome display">Welcome To</div>
  <h1 class="hero-title display">SnackOrbit</h1>
  <p class="hero-lead">Lorem ipsum dolor sit amet, onsectetur adipiscing elit, sed do</p>
  <a class="btn hero-cta">Get A Free Vending Machine</a>
</section>

<section class="who">
  <div class="ph who-img" role="img" aria-label="White snack vending machine stocked with snacks on a teal backdrop"></div>
  <h2 class="display">Who We Are</h2>
  <p>Welcome to SnackOrbit, where snacking meets delight! We're not just about vending machines; we're your culinary companions, your flavor curators, and your secret stash of happiness.Mark and Jenna, the dynamic duo behind SnackOrbit, have a passion for all things tasty. With backgrounds in sales and a penchant for personal connections, they've transformed the vending experience into an art form.</p>
  <a class="btn">Read More</a>
</section>

<section class="why">
  <h2 class="display">Why Choose SnackOrbit?</h2>
  <div class="why-machine" role="img" aria-label="Blue snack vending machine filled with chips and candy bars"></div>

  <svg class="why-icon" style="left:111px;top:143px" width="44" height="40" viewBox="0 0 44 40" aria-hidden="true"><path d="M22 38 L5 21 A10.5 10.5 0 0 1 22 7 A10.5 10.5 0 0 1 39 21 Z" fill="#fff"/></svg>
  <div class="why-item" style="left:111px;top:195px">
    <h3>1. Local Love</h3>
    <p>We celebrate the heart of Michigan by partnering with local legends. Say hello to Birchwood Jerky and Pine Shore Chips—our hometown heroes.</p>
    <a>Read More</a>
  </div>

  <svg class="why-icon" style="left:111px;top:463px" width="56" height="50" viewBox="0 0 56 50" aria-hidden="true"><circle cx="18" cy="12" r="10" fill="#fff"/><path d="M2 48 Q2 26 18 26 Q34 26 34 48 Z" fill="#fff"/><circle cx="46" cy="28" r="8" fill="none" stroke="#fff" stroke-width="3"/></svg>
  <div class="why-item" style="left:111px;top:512px">
    <h3>2. Unleash Your Cravings</h3>
    <p>SnackOrbit isn't bound by corporate ties. We're the rebels of the vending world. Craving a bag of crispy, kettle-cooked chips? done.Hankering for jerky that packs a punch? We've got you covered.</p>
    <a>Read More</a>
  </div>

  <svg class="why-icon" style="left:1031px;top:130px" width="56" height="56" viewBox="0 0 56 56" aria-hidden="true"><circle cx="28" cy="28" r="26" fill="#fff"/><circle cx="28" cy="28" r="17" fill="none" stroke="#26306e" stroke-width="3"/><path d="M19 28 L26 35 L38 22" fill="none" stroke="#26306e" stroke-width="4" stroke-linecap="round"/></svg>
  <div class="why-item right" style="left:789px;top:195px">
    <h3>3. Quality Meets Convenience</h3>
    <p>Imagine this: You're mid-meeting, and your stomach growls. Fear not! SnackOrbit's machines offer top-notch snacks and beverages. It's like having a mini food festival at your fingertips.</p>
    <a>Read More</a>
  </div>

  <svg class="why-icon" style="left:1034px;top:445px" width="54" height="54" viewBox="0 0 54 54" aria-hidden="true"><circle cx="27" cy="27" r="24" fill="none" stroke="#fff" stroke-width="3"/><path d="M3 27 H51 M27 3 Q14 27 27 51 M27 3 Q40 27 27 51" fill="none" stroke="#fff" stroke-width="2.5"/></svg>
  <div class="why-item right" style="left:789px;top:510px">
    <h3>4. Pandemic-Proof &amp; Recession<br>-Ready</h3>
    <p>Life throws curveballs, but SnackOrbit stands strong. Our vending machines are theunsung heroes of resilience.</p>
    <a>Read More</a>
  </div>
</section>

<section class="services">
  <h2 class="display">Our Services</h2>
  <div class="tab active" style="left:210px;width:181px">Food &amp; Snaks</div>
  <div class="tab" style="left:398px;width:164px">Drinks &amp; Cofee</div>
  <div class="tab" style="left:584px;width:191px">Gumball &amp; Candy</div>
  <div class="tab" style="left:800px;width:190px">Cold &amp; Frozen</div>
  <div class="svc-title display">FOOD &amp; SNAKS</div>
  <div class="ph svc-icon" role="img" aria-label="Drink cup and burger icon"></div>
  <p class="svc-text">Lorem ipsum dolor sit amet, consectetur adipiscing elit, sed mpor incididunt ut labore et dolore magna aliqua. Quis ipsum spendisse ultrices gravida. Risus commodo viverra maecenas ccumsan lacus vel facilisis.Lorem ipsum dolor sit amet, onsectetur it,sed do usmod tempor incididunt ut labore et lore magna liqua. Quis spendissehy ultrices gravida. Risus commodo viverra maecenas accumsan lacus vel facilisis. Lorem ipsum dolor sit amet, consectetur adipiscingfgs elit, sed do eiusmod tempor incididunt ut labore et dolore magna aliqua. Quis ipsum suspendisse ultrices gravida. Risus commodosd viverra maecenas accumsan lacus vel facilisis.</p>
  <a class="btn svc-btn">Learn More</a>
  <div class="ph svc-machine" role="img" aria-label="Silver and blue snack vending machine"></div>
</section>

<section class="products">
  <h2 class="display">Our Products</h2>
  <article class="card" style="left:111px">
    <div class="card-img" role="img" aria-label="White drinks and coffee vending machine" style="background:linear-gradient(180deg,#f2f2f2,#dcdcdc)"></div>
    <h3>DRINKS &amp; COFEE<br>VENDING MACHINE</h3>
    <div class="price">$256</div>
    <a class="btn">Buy Now</a>
  </article>
  <article class="card" style="left:441px">
    <div class="card-img" role="img" aria-label="Colorful teal gumball and candy vending machine" style="background:linear-gradient(180deg,#9ad7dc,#5fbfc6)"></div>
    <div class="badge" style="left:268px;top:18px"><svg width="18" height="16" viewBox="0 0 44 40" aria-hidden="true"><path d="M22 38 L5 21 A10.5 10.5 0 0 1 22 7 A10.5 10.5 0 0 1 39 21 Z" fill="#e02424"/></svg></div>
    <div class="badge" style="left:268px;top:64px">NEW</div>
    <h3>GUMBALL &amp; CANDY<br>VENDING MACHINE</h3>
    <div class="price">$226</div>
    <a class="btn">Buy Now</a>
  </article>
  <article class="card" style="left:772px">
    <div class="card-img" role="img" aria-label="Black cold and frozen vending machine stocked with drinks" style="background:linear-gradient(180deg,#e6e6f4,#b9bbd8)"></div>
    <h3 class="alt">COLD &amp; FROZEN<br>VENDING MACHINE</h3>
    <div class="price">$156</div>
    <a class="btn">Buy Now</a>
  </article>
  <div class="dots"><span></span><span class="on"></span><span></span></div>
</section>

<section class="cta">
  <h2 class="display">READY TO EXPERIENCE THE SNACKORBIT DIFFERENCE?</h2>
  <p>Sign up now and let's connect. Taste the future of snacking firsthand! Contact us todayand explore how our vending magic can elevate your space.</p>
  <a class="btn">Learn More</a>
</section>

<footer class="site-footer">
  <div class="foot-brand">SnackOrbit</div>
  <span class="social" style="left:248px" role="img" aria-label="Social profile"></span>
  <span class="social" style="left:315px" role="img" aria-label="Social profile"></span>
  <span class="social" style="left:383px" role="img" aria-label="Social profile"></span>

  <div class="foot-col"><h4 style="left:619px">Quick Links</h4></div>
  <ul class="foot-links">
    <li>Home</li>
    <li>About SnackOrbit</li>
    <li>Why Choose SnackOrbit?</li>
    <li>Products &amp; Services</li>
    <li>Contact Us</li>
  </ul>

  <div class="foot-col"><h4 style="left:841px">Contact Us</h4></div>
  <div class="contact-row" style="top:175px">
    <i><svg width="22" height="16" viewBox="0 0 22 16" aria-hidden="true"><rect x="1" y="1" width="20" height="14" rx="2" fill="#fff"/><path d="M1 2 L11 9 L21 2" fill="none" stroke="#2d5a27" stroke-width="2"/></svg></i>
    <span>Info@snackorbit.com</span>
  </div>
  <div class="contact-row" style="top:237px">
    <i><svg width="18" height="24" viewBox="0 0 18 24" aria-hidden="true"><path d="M9 23 C3 15 1 12 1 8.5 A8 8 0 0 1 17 8.5 C17 12 15 15 9 23 Z" fill="#fff"/><circle cx="9" cy="8.5" r="3" fill="#2d5a27"/></svg></i>
    <span>Lorem ipsum dolor sit<br>SnackOrbit.USA</span>
  </div>
  <div class="contact-row" style="top:302px">
    <i><svg width="20" height="20" viewBox="0 0 24 24" aria-hidden="true"><path d="M6.6 10.8a15 15 0 0 0 6.6 6.6l2.2-2.2a1 1 0 0 1 1-.25 11.4 11.4 0 0 0 3.6.57 1 1 0 0 1 1 1V20a1 1 0 0 1-1 1A17 17 0 0 1 3 4a1 1 0 0 1 1-1h3.5a1 1 0 0 1 1 1c0 1.25.2 2.45.57 3.57a1 1 0 0 1-.25 1z" fill="#fff"/></svg></i>
    <span>+1(555)014 2290</span>
  </div>

  <p class="copyright">Copyright © 2024 SnackOrbit | All Rights Reserved</p>
</footer>

</body>
</html>
```